Fitness Equipment & Service

I want to make the card eye catching and fun. We are called Corvane Motion Limited and we are based in Wales. We sell, install and service all types of fitness equipment from Skipping ropes, right through the Dumbbells, Kettle bells and Barbells through to state of the art Treadmills, Running Machines and Strength Equipment. We also design and install changing room furniture and lockers.

TYPOGRAPHY
We would like to use Futrura. Futura has an appearance of efficiency and forwardness. The typeface is derived
from simple geometric forms (near-perfect circles, triangles and squares) and is based on strokes of
near-even weight, which are low in contrast. This is most visible in the almost perfectly round stroke of
the o, which is nonetheless slightly ovoid.
The lowercase has tall ascenders, which rise above the cap line. The uppercase
characters present proportions similar to those of classical Roman capitals.

TYPOGRAPHIC CONSIDERATIONS
No Strike though
No Horizontal Scaling
No Drop Shadows
No Effects
Never use less than 120% Leading

OUR CORPORATE COLOURS
BRAND GUIDELINES
We were thinking that our primary colour palette consists of the Acid Green (Pantone 382) and Process Black.

We work closely with tquarly Ltd and would like to include their name on the card somewhere. I have attached images of the other brands that we work with as an idea or the small icons I have included that illustrate what we do?. I have very kindly been given permission to use any of the images off the files that I have included below, so I hope these help. I will include these below. I would be open to suggestions if it made the card more striking Can you do it?
Updates

Hi All, Just wanted to add a few thoughts but you are the guys with the creative visions (thats why are here) We are based in Wales, UK and we would be open to lots of different ideas on a theme but must be eye catching, Bold and FUN. If you can or think that the Welsh or any dragon could be put in there then go for it (its not a must have) We have also added some ideas for colour but again its over to you!! GO FOR IT ! Thanks and look forward to your visions! Owen

Hi All, Just thought I would sen through the contact details that need to be on the card. (if you want to play around with icons instead of the wording twitter, Facebook, go for it): Corvane Motion Limited Owen Pritchard Managing Director Mob: +44 (0)7582 913 406 e-mail: sales@corvanemotion.co.uk Web: Corvanemotion.co.uk twitter: @motionLetterbin Facebook: Corvane Motion Limited

```html
<!DOCTYPE html>
<html lang="en">
<head>
<meta charset="utf-8">
<title>Corvane Motion Limited – Business Card</title>
<link href="https://fonts.googleapis.com/css2?family=Jost:wght@400;500;700&display=swap" rel="stylesheet">
<style>
  :root {
    --backdrop: #e9e6e1;
    --card-white: #f7f8fa;
    --blue-deep: #1b57a8;
    --blue-mid: #2b74c4;
    --blue-light: #4a97dc;
    --blue-dark: #16407e;
    --blue-ink: #0f2f63;
    --tile-pale: #c9d7e8;
    --navy: #25286e;
    --rule: #1c2f7a;
    --text-light: #ffffff;
    --icon-tile: #dfe6ef;
  }
  * { box-sizing: border-box; margin: 0; padding: 0; }
  html, body {
    width: 1200px; height: 892px; overflow: hidden;
    background: var(--backdrop);
    font-family: "Jost", "Futura", sans-serif;
  }
  .canvas { position: relative; width: 1200px; height: 892px; }

  .card {
    position: absolute;
    width: 640px; height: 376px;
    border-radius: 4px;
    overflow: hidden;
    box-shadow: 0 6px 18px rgba(0,0,0,0.18);
  }
  .card--front { left: 280px; top: 50px; display: flex; }
  .card--back  { left: 280px; top: 466px; background: var(--card-white); padding: 12px; }

  /* front: brand panel */
  .brand-panel {
    width: 34%;
    background: var(--card-white);
    display: flex; flex-direction: column;
    align-items: center; justify-content: center;
    gap: 18px;
  }
  .brand-circle {
    width: 118px; height: 118px; border-radius: 50%;
    background: var(--navy);
  }
  .brand-name {
    color: var(--navy);
    font-weight: 500;
    font-size: 21px;
    line-height: 1.25;
    text-align: center;
    letter-spacing: 0.04em;
  }

  /* front: contact panel */
  .contact-panel {
    flex: 1;
    background: linear-gradient(160deg, var(--blue-light) 0%, var(--blue-mid) 45%, var(--blue-deep) 100%);
    color: var(--text-light);
    padding: 30px 30px 28px 28px;
    display: flex; flex-direction: column; align-items: flex-end;
  }
  .person-name { font-size: 27px; font-weight: 700; line-height: 1.2; }
  .person-role { font-size: 14px; font-weight: 500; line-height: 1.3; margin-bottom: 34px; }

  .contact-list { list-style: none; display: flex; flex-direction: column; align-items: flex-end; gap: 4px; }
  .contact-item {
    display: flex; align-items: center; gap: 10px;
    font-size: 17.5px; font-weight: 500; line-height: 1.3;
  }
  .contact-icon {
    width: 15px; height: 15px; flex: none;
    background: var(--icon-tile); border-radius: 2px;
    display: flex; align-items: center; justify-content: center;
  }
  .contact-icon svg { width: 11px; height: 11px; }

  .divider {
    align-self: stretch;
    height: 2px; background: var(--rule);
    margin: 16px 0 16px;
  }
  .social-tile {
    width: 22px; height: 22px; flex: none;
    background: var(--icon-tile); border-radius: 3px;
  }

  /* back: tile mosaic */
  .back-mosaic {
    position: relative;
    width: 100%; height: 100%;
    border-radius: 2px;
    overflow: hidden;
    display: grid;
    grid-template-columns: repeat(7, 1fr);
    grid-template-rows: repeat(4, 1fr);
  }
  .tile { display: flex; align-items: center; justify-content: center; }
  .tile--light { background: var(--blue-light); }
  .tile--mid   { background: var(--blue-mid); }
  .tile--deep  { background: var(--blue-deep); }
  .tile--dark  { background: var(--blue-dark); }
  .tile--ink   { background: var(--blue-ink); }
  .tile--pale  { background: var(--tile-pale); }
  .tile-icon {
    width: 38px; height: 38px;
    border-radius: 8px;
    background: rgba(255,255,255,0.9);
  }
  .tile--pale .tile-icon { background: var(--card-white); }

  .back-brand {
    position: absolute; left: 0; top: 0;
    width: 264px; height: 88px;
    padding-left: 22px;
    display: flex; align-items: center; gap: 12px;
    background: var(--blue-deep);
    color: var(--text-light);
    font-weight: 500; font-size: 17px; line-height: 1.25;
  }
  .back-brand-circle {
    width: 48px; height: 48px; border-radius: 50%; flex: none;
    background: var(--card-white);
  }
</style>
</head>
<body>
<main class="canvas">

  <section class="card card--front" aria-label="Business card front">
    <div class="brand-panel">
      <div class="brand-circle"></div>
      <p class="brand-name">Corvane Motion<br>Limited</p>
    </div>

    <div class="contact-panel">
      <h1 class="person-name">Owen Pritchard</h1>
      <p class="person-role">Managing Director</p>

      <ul class="contact-list">
        <li class="contact-item">+44 (0)7582 913 406
          <span class="contact-icon">
            <svg viewBox="0 0 12 12"><path d="M2.5 1h2l1 2.6-1.3 1a6 6 0 0 0 3.2 3.2l1-1.3 2.6 1v2A1 1 0 0 1 10 11 9 9 0 0 1 1 2a1 1 0 0 1 1.5-1z" fill="#1b57a8"/></svg>
          </span>
        </li>
        <li class="contact-item">sales@corvanemotion.co.uk
          <span class="contact-icon">
            <svg viewBox="0 0 12 12"><rect x="1" y="2.5" width="10" height="7" fill="none" stroke="#1b57a8" stroke-width="1.3"/><path d="M1 2.5l5 4 5-4" fill="none" stroke="#1b57a8" stroke-width="1.3"/></svg>
          </span>
        </li>
        <li class="contact-item">Corvanemotion.co.uk
          <span class="contact-icon">
            <svg viewBox="0 0 12 12"><circle cx="6" cy="6" r="4.8" fill="none" stroke="#1b57a8" stroke-width="1.2"/><path d="M1.2 6h9.6M6 1.2c-2.4 2.6-2.4 7 0 9.6M6 1.2c2.4 2.6 2.4 7 0 9.6" fill="none" stroke="#1b57a8" stroke-width="1"/></svg>
          </span>
        </li>
      </ul>

      <div class="divider"></div>

      <ul class="contact-list">
        <li class="contact-item">@motionLetterbin <span class="social-tile"></span></li>
        <li class="contact-item">Corvane Motion Limited <span class="social-tile"></span></li>
      </ul>
    </div>
  </section>

  <section class="card card--back" aria-label="Business card back">
    <div class="back-mosaic">
      <!-- row 1 -->
      <div class="tile tile--deep"></div>
      <div class="tile tile--deep"></div>
      <div class="tile tile--deep"></div>
      <div class="tile tile--light"></div>
      <div class="tile tile--mid"></div>
      <div class="tile tile--light"></div>
      <div class="tile tile--mid"></div>
      <!-- row 2 -->
      <div class="tile tile--pale"><span class="tile-icon" role="img" aria-label="Treadmill icon"></span></div>
      <div class="tile tile--mid"><span class="tile-icon" role="img" aria-label="Cross trainer icon"></span></div>
      <div class="tile tile--dark" role="img" aria-label="Dumbbell photograph detail"></div>
      <div class="tile tile--deep"><span class="tile-icon" role="img" aria-label="Locker icon"></span></div>
      <div class="tile tile--light"></div>
      <div class="tile tile--mid"><span class="tile-icon" role="img" aria-label="Rowing machine icon"></span></div>
      <div class="tile tile--deep"></div>
      <!-- row 3 -->
      <div class="tile tile--light"></div>
      <div class="tile tile--dark" role="img" aria-label="Dumbbell photograph detail"></div>
      <div class="tile tile--mid"><span class="tile-icon" role="img" aria-label="Boxing gloves icon"></span></div>
      <div class="tile tile--ink" role="img" aria-label="Dumbbell photograph detail"></div>
      <div class="tile tile--deep"></div>
      <div class="tile tile--light"><span class="tile-icon" role="img" aria-label="Skipping rope icon"></span></div>
      <div class="tile tile--mid"></div>
      <!-- row 4 -->
      <div class="tile tile--mid"></div>
      <div class="tile tile--deep"></div>
      <div class="tile tile--ink" role="img" aria-label="Dumbbell photograph detail"></div>
      <div class="tile tile--dark"><span class="tile-icon" role="img" aria-label="Weight plate icon"></span></div>
      <div class="tile tile--mid"></div>
      <div class="tile tile--deep"></div>
      <div class="tile tile--light"></div>

      <div class="back-brand">
        <span class="back-brand-circle"></span>
        <span>Corvane Motion<br>Limited</span>
      </div>
    </div>
  </section>

</main>
</body>
</html>
```